BUSINESS CARD - HALLORAN FIELD SERVICES

I would like to create a business card for my fertilizer spreading business. I would like to incorporate my existing logo and also a description of the services offered. The business card will be given to farmers so must be kept simple but effective. It will also be left in stores so much also be eye catching in order to stand out from other cards.

Target Market(s)

FARMERS

Requirements
Must have
• FRONT OF CARD = EXISTING LOGO + "CUSTOMISED SPREADING" below the logo

REAR Of CARD = SERVICES OFFERED AND CONTACT DETAILS

- Bulk fertilizer including Lime, Gypsum, Manure & Compost
- Granular fertilizer including Single Super, Urea, Gran-am, & Custom Blends
- Modern equipment - Autosteer & Variable Rate Capable
- Friendly & Reliable Service
- Contact Gus: 0417 552 308
Nice to have
• utilize same color scheme as existing logo

```html
<!DOCTYPE html>
<html lang="en">
<head>
<meta charset="utf-8">
<title>Halloran Field Services – Business Card</title>
<link rel="stylesheet" href="https://fonts.googleapis.com/css2?family=Arimo:wght@400;700&display=swap">
<style>
  :root {
    --backdrop: #1f1f1f;
    --card-white: #ffffff;
    --card-grey: #555556;
    --ink-grey: #4b4b4d;
    --accent-orange: #f39a1e;
    --text-light: #ffffff;
    --rule-soft: rgba(255, 255, 255, 0.25);
  }
  * { box-sizing: border-box; margin: 0; padding: 0; }
  html, body {
    width: 1200px;
    height: 1040px;
    overflow: hidden;
    background: var(--backdrop);
    font-family: "Arimo", Arial, sans-serif;
  }
  .stage {
    width: 1200px;
    height: 1040px;
    display: flex;
    flex-direction: column;
    align-items: center;
    justify-content: center;
    gap: 60px;
  }
  .card {
    width: 600px;
    height: 343px;
    position: relative;
    display: flex;
    flex-direction: column;
    align-items: center;
    justify-content: center;
    text-align: center;
  }
  .card--front {
    background: var(--card-white);
    border-radius: 90px 0 90px 0;
  }
  .card--back {
    background: var(--card-grey);
    border-radius: 0 90px 0 90px;
    color: var(--text-light);
  }
  .brand {
    display: flex;
    align-items: center;
    gap: 16px;
  }
  .brand__dot {
    width: 44px;
    height: 44px;
    border-radius: 50%;
    background: var(--ink-grey);
    flex: none;
  }
  .brand__name {
    font-weight: 700;
    font-size: 34px;
    letter-spacing: 0.5px;
    color: var(--ink-grey);
    text-transform: uppercase;
  }
  .tagline {
    margin-top: 26px;
    font-size: 21px;
    letter-spacing: 3px;
    color: var(--accent-orange);
    text-transform: uppercase;
  }
  .services {
    list-style: none;
    font-size: 17px;
    line-height: 1.4;
    padding: 0 30px;
  }
  .services__item--gap { margin-top: 6px; }
  .divider {
    width: 260px;
    height: 1px;
    background: var(--rule-soft);
    margin: 16px 0 14px;
  }
  .contact {
    font-size: 28px;
    color: var(--accent-orange);
  }
</style>
</head>
<body>
  <main class="stage">
    <section class="card card--front" aria-label="Card front">
      <div class="brand">
        <span class="brand__dot" aria-hidden="true"></span>
        <span class="brand__name">Halloran Field Services</span>
      </div>
      <p class="tagline">Customised Spreading</p>
    </section>

    <section class="card card--back" aria-label="Card back">
      <ul class="services">
        <li>Bulk fertilizer including Lime, Gypsum, Manure &amp; Compost</li>
        <li class="services__item--gap">Granular fertilizer including Single Super, Urea<br>Gran-am, &amp; Custom Blends</li>
        <li class="services__item--gap">Modern equipment</li>
        <li>Autosteer &amp; Variable Rate Capable</li>
        <li>Friendly &amp; Reliable Service</li>
      </ul>
      <div class="divider" aria-hidden="true"></div>
      <p class="contact">Contact Gus: 0417 552 308</p>
    </section>
  </main>
</body>
</html>
```